Business Card Design for Brindle Consulting

I need business cards for a new company I have started called Brindle Consulting. Brindle Consulting is a new business based out of Columbus Ohio. I will be operating in Ohio as well as nationwide. Brindle Consulting is a professional organization designed to fit your organization's specific needs. We are dedicated to the success of organizations. We handle human resource management, leadership coaching and development, executive training, team building, personality inventories and searches, performance evaluations, temp. services, custom solutions and more. Brindle consulting services a variety of industries such as government agencies, educational systems, board of directors, construction services and more, please visit our website for a full list of services (the website will be important).

I leave the design to you. I am a 45 year old male. I was in the education field for 21 years and 11 years as a superintendent. I like the colors red and black. Don't know what works, I will leave that to you as well. I would like to have it be catchy yet masculine. I have been associated with many organizations over the years both public and private, and will be reaching out to the public and private sector.

I do need a logo...so I leave that to you as well. Company name is Brindle Consulting.

Industry/Entity Type

Construction

Contact Information for Business Card

Gordon T. Brindle, President
Brindle Consulting
48 W.Fifth St. Suite 305
Arcade at Halvern Court
Columbus, Ohio 43287

Phone : 330-555-4178
email : gbrindle@brindleadvise.example
web : www.brindleadvise.example
twitter : @brindleadvise
facebook : Brindle Consulting

```html
<!DOCTYPE html>
<html lang="en">
<head>
<meta charset="utf-8">
<title>Brindle Consulting – Business Card</title>
<link rel="stylesheet" href="https://fonts.googleapis.com/css2?family=Orbitron:wght@500&family=Roboto:wght@400&display=swap">
<style>
  :root {
    --page-bg: #8c8c8c;
    --card-dark: #141414;
    --card-mid: #2b2b2b;
    --accent-blue: #1ea9ea;
    --title-gold: #d9b36a;
    --text-light: #d6d6d6;
  }
  html, body {
    margin: 0;
    padding: 0;
    width: 1200px;
    height: 988px;
    overflow: hidden;
    background: var(--page-bg);
  }
  .canvas {
    width: 1200px;
    height: 988px;
    display: flex;
    flex-direction: column;
    align-items: center;
    justify-content: center;
    gap: 60px;
  }
  .card {
    position: relative;
    width: 640px;
    height: 366px;
    background: radial-gradient(ellipse at 50% 45%, var(--card-mid) 0%, var(--card-dark) 75%);
    box-shadow: 0 6px 18px rgba(0,0,0,0.35);
    overflow: hidden;
  }
  .card__band {
    position: absolute;
    top: 0; left: 0; right: 0;
    height: 16px;
    background: var(--accent-blue);
  }
  .card__rule {
    position: absolute;
    left: 0; right: 0;
    height: 3px;
    background: var(--accent-blue);
  }
  .rule--upper { top: 130px; }
  .rule--lower { top: 258px; }
  .company-name {
    position: absolute;
    left: 0; right: 0;
    text-align: center;
    font-family: 'Orbitron', sans-serif;
    font-weight: 500;
    color: var(--accent-blue);
    letter-spacing: 3px;
    text-transform: uppercase;
    margin: 0;
    line-height: 1;
  }
  .card--info .company-name {
    top: 72px;
    font-size: 24px;
  }
  .card--logo .company-name {
    top: 170px;
    font-size: 26px;
  }
  .person {
    position: absolute;
    left: 30px;
    top: 208px;
    font-family: 'Orbitron', sans-serif;
    font-weight: 500;
  }
  .person__name {
    color: var(--accent-blue);
    font-size: 14px;
    line-height: 16px;
    letter-spacing: 1.5px;
    text-transform: uppercase;
    margin: 0 0 8px;
  }
  .person__title {
    color: var(--title-gold);
    font-size: 10px;
    line-height: 12px;
    letter-spacing: 1.5px;
    text-transform: uppercase;
    margin: 0;
  }
  .contacts {
    position: absolute;
    left: 240px;
    top: 150px;
    display: grid;
    grid-template-columns: 185px 185px;
    row-gap: 14px;
    column-gap: 14px;
    font-family: 'Roboto', sans-serif;
    font-size: 11px;
    line-height: 14px;
    color: var(--text-light);
  }
  .contact {
    display: flex;
    align-items: center;
    gap: 7px;
    white-space: nowrap;
  }
  .contact--wide { grid-column: 1 / span 2; }
  .contact__icon {
    width: 14px;
    height: 14px;
    flex: none;
  }
</style>
</head>
<body>
<main class="canvas">
  <section class="card card--info" aria-label="Business card, contact side">
    <div class="card__band"></div>
    <h1 class="company-name">Brindle Consulting</h1>
    <div class="card__rule rule--upper"></div>

    <div class="contacts">
      <div class="contact">
        <svg class="contact__icon" viewBox="0 0 14 14" aria-hidden="true"><circle cx="7" cy="7" r="7" fill="var(--accent-blue)"/><path d="M4.5 3.5l1.5 0 .6 1.8-1 .7a5 5 0 0 0 2.4 2.4l.7-1 1.8.6 0 1.5c-3.5.3-6.3-2.5-6-6z" fill="#111"/></svg>
        <span>330 555 4178</span>
      </div>
      <div class="contact">
        <svg class="contact__icon" viewBox="0 0 14 14" aria-hidden="true"><circle cx="7" cy="7" r="7" fill="var(--accent-blue)"/><path d="M4.5 3.5l1.5 0 .6 1.8-1 .7a5 5 0 0 0 2.4 2.4l.7-1 1.8.6 0 1.5c-3.5.3-6.3-2.5-6-6z" fill="#111"/></svg>
        <span>330 555 4190</span>
      </div>
      <div class="contact">
        <svg class="contact__icon" viewBox="0 0 14 14" aria-hidden="true"><circle cx="7" cy="7" r="7" fill="var(--accent-blue)"/><rect x="3.5" y="4.5" width="7" height="5" fill="none" stroke="#111" stroke-width="1"/><path d="M3.5 4.5l3.5 3 3.5-3" fill="none" stroke="#111" stroke-width="1"/></svg>
        <span>gbrindle@brindleadvise.example</span>
      </div>
      <div class="contact">
        <svg class="contact__icon" viewBox="0 0 14 14" aria-hidden="true"><circle cx="7" cy="7" r="7" fill="var(--accent-blue)"/><circle cx="7" cy="7" r="3.5" fill="none" stroke="#111" stroke-width="1"/><path d="M3.5 7h7M7 3.5v7" stroke="#111" stroke-width="0.8"/></svg>
        <span>www.brindleadvise.example</span>
      </div>
      <div class="contact contact--wide">
        <svg class="contact__icon" viewBox="0 0 14 14" aria-hidden="true"><circle cx="7" cy="7" r="7" fill="var(--accent-blue)"/><path d="M7 11S4.2 7.8 4.2 6a2.8 2.8 0 0 1 5.6 0C9.8 7.8 7 11 7 11z" fill="#111"/><circle cx="7" cy="6" r="1" fill="var(--accent-blue)"/></svg>
        <span>48 W.Fifth St. Suite 305 Columbus</span>
      </div>
    </div>

    <div class="person">
      <p class="person__name">Gordon T. Brindle</p>
      <p class="person__title">President</p>
    </div>
    <div class="card__rule rule--lower"></div>
  </section>

  <section class="card card--logo" aria-label="Business card, name side">
    <div class="card__band"></div>
    <h2 class="company-name">Brindle Consulting</h2>
  </section>
</main>
</body>
</html>
```